Occasions chocolate packaging

We are looking for 7 packaging designs for bars of chocolate.

Each design needs to be different and we’re not looking for a consistent brand or branding message across the designs. Inspiration should come from gift/occasion cards. Fun, simple, bold, vibrant colours and eye catching, i.e. not vintage or just text.

The front of the packaging should have the main message on and is free of any branding. You don’t need to design the back, just simply allow the main background colour or design pattern to continue around.

These are the different designs we are after, I’ve added in some text for each to give you some guidance but feel free to play around with the message if it suits the design better.

1) Mum
‘The best mum’, ‘Best mum in the World’, ‘Number 1 Mum’

2) Dad
‘The Best Dad’, ‘Best Dad Ever’, ‘Number 1 Dad’, ‘You’re my hero Dad’

3) Husband
‘Best Husband in the World’, ‘Husband I Love You’, ‘Darling Husband’

4) Wife
‘Best Wife in the World’, ‘For my Wonderful Wife’, ‘My Beautiful Wife’

5) Congratulations
Simple one, just Congratulations

6) Thinking of you
Try and keep this neutral as it could be used for happy and sad situations.

7) Thank you
Keep this gender neutral.

Sides:
The sides need to have the following text:

FINE BELGIAN DARK CHOCOLATE
infused with Orange

Back:
The main colour of the front should continue all the way around, we will place a box with the contents and bar code on here ourselves so no need to do anything.

Dimensions:
Attached in the document, front of package is 85mm by 190mm.

The packaging is made from folded card, the first blank part is for gluing the back on to.

Reason: I'm extending the deadline as I've only received 1 design so far which has followed the brief. Although I do like it, I would like to see at least some competition...

```html
<!DOCTYPE html>
<html lang="en">
<head>
<meta charset="utf-8">
<title>Best Dad in the World – Chocolate Bar Sleeve</title>
<link rel="stylesheet" href="https://fonts.googleapis.com/css2?family=Oswald:wght@700&family=Montserrat:wght@600&display=swap">
<style>
  :root {
    --backdrop: #e4e5e7;
    --sleeve-blue: #1f4fd6;
    --sleeve-blue-light: #2f66ee;
    --sleeve-blue-deep: #1a3fb8;
    --label-band: #1a3ca8;
    --ink-white: #ffffff;
    --art-white: #ffffff;
    --art-blush: #f8d3e3;
    --art-pink: #f2a6c6;
  }
  * { box-sizing: border-box; margin: 0; padding: 0; }
  html, body {
    width: 1200px;
    height: 960px;
    overflow: hidden;
    background: var(--backdrop);
  }
  .sleeve {
    position: absolute;
    left: 380px;
    top: 70px;
    display: flex;
    height: 820px;
  }
  .sleeve-side {
    width: 64px;
    height: 100%;
    background: linear-gradient(180deg, var(--sleeve-blue-deep), var(--sleeve-blue));
    position: relative;
    border-right: 1px solid rgba(255,255,255,0.12);
  }
  .side-text {
    position: absolute;
    left: 50%;
    top: 50%;
    transform: translate(-50%, -50%) rotate(-90deg);
    white-space: nowrap;
    color: var(--ink-white);
    font-family: "Montserrat", "Century Gothic", sans-serif;
    font-weight: 600;
    display: flex;
    align-items: baseline;
    gap: 14px;
  }
  .side-title { font-size: 20px; letter-spacing: 3px; }
  .side-flavour { font-size: 16px; letter-spacing: 2px; }
  .sleeve-front {
    width: 367px;
    height: 100%;
    background: radial-gradient(ellipse at 50% 40%, var(--sleeve-blue-light), var(--sleeve-blue) 60%, var(--sleeve-blue-deep));
    position: relative;
    overflow: hidden;
  }
  .hero-art {
    position: absolute;
    left: 28px;
    top: 58px;
    width: 300px;
    height: 318px;
    border-radius: 28px;
    background: linear-gradient(200deg, var(--art-pink) 0%, var(--art-blush) 38%, var(--art-white) 78%);
    box-shadow: 0 6px 18px rgba(10, 30, 110, 0.35);
  }
  .headline {
    position: absolute;
    left: 0;
    right: 0;
    top: 380px;
    text-align: center;
    color: var(--ink-white);
    font-family: "Oswald", "Bebas Neue", sans-serif;
    font-weight: 700;
    text-transform: uppercase;
    line-height: 0.9;
    text-shadow: 0 3px 6px rgba(10, 30, 110, 0.35);
  }
  .headline-best { display: block; font-size: 108px; letter-spacing: -1px; }
  .headline-dad { display: block; font-size: 146px; letter-spacing: -2px; margin-top: 6px; }
  .headline-tail { display: block; font-size: 38px; letter-spacing: -1px; margin-top: 10px; }
  .flavour-band {
    position: absolute;
    left: 12px;
    right: 12px;
    bottom: 10px;
    height: 130px;
    border-radius: 14px;
    background: var(--label-band);
    color: var(--ink-white);
    font-family: "Montserrat", "Century Gothic", sans-serif;
    font-weight: 600;
    text-align: center;
    padding-top: 20px;
  }
  .flavour-title { font-size: 26px; line-height: 1.12; letter-spacing: 1.5px; }
  .flavour-note { font-size: 15px; letter-spacing: 2px; margin-top: 8px; }
</style>
</head>
<body>
  <div class="sleeve">
    <div class="sleeve-side">
      <div class="side-text">
        <span class="side-title">FINE BELGIAN DARK CHOCOLATE</span>
        <span class="side-flavour">infused with Orange</span>
      </div>
    </div>
    <div class="sleeve-front">
      <div class="hero-art" role="img" aria-label="White silhouette of a father bending down to kiss his small daughter, with a pink heart behind them"></div>
      <h1 class="headline">
        <span class="headline-best">Best</span>
        <span class="headline-dad">Dad</span>
        <span class="headline-tail">In the World</span>
      </h1>
      <div class="flavour-band">
        <p class="flavour-title">FINE BELGIAN<br>DARK CHOCOLATE</p>
        <p class="flavour-note">INFUSED WITH ORANGE</p>
      </div>
    </div>
  </div>
</body>
</html>
```